Insurance Agency website design for Brellow Cover Insurance, LP

Build a website for Brellow Cover Insurance, LP which sells Homeowners, Auto, Renters, Condo, Flood, Disability, Life, Umbrella, and health insurance. We need the coolest insurance agency website out there to get quotes, contact us, or get additional information. Please list the following insurance companies we work with: Varnix, Ostle, Meridale Mutual, Quillor, Dunmarrow, KGZ, and Pellwick.

Make a design similar to https://www.fernagentry.com/

Selling personal insurance policies

```html
<!DOCTYPE html>
<html lang="en">
<head>
<meta charset="utf-8">
<title>Brellow Cover Insurance, LP</title>
<link href="https://fonts.googleapis.com/css2?family=Montserrat:wght@400;500;600;700;800&display=swap" rel="stylesheet">
<style>
:root{
  --navy:#0d2470;
  --blue:#0e5fa8;
  --link:#1f6fbf;
  --ink:#1b1b1b;
  --text:#444;
  --light:#f1f1f1;
  --line:#d9d9d9;
  --white:#fff;
}
*{box-sizing:border-box;margin:0;padding:0}
html,body{width:1200px;height:4532px;overflow:hidden}
body{position:relative;font-family:'Montserrat',sans-serif;color:var(--ink);background:var(--white)}
.abs{position:absolute}
.topbar{left:0;top:0;width:1200px;height:7px;background:var(--navy)}
.header{left:0;top:7px;width:1200px;height:97px;background:var(--white)}
.brand{display:flex;align-items:center;gap:12px}
.brand-mark{width:50px;height:50px;border:3px solid var(--blue);border-radius:4px}
.brand-name{color:var(--blue);line-height:1;font-weight:500}
.brand-name b{display:block;font-weight:700}
.header .brand{position:absolute;left:110px;top:22px}
.header .brand-name{font-size:21px}
.header .brand-name b{font-size:26px}
.nav{position:absolute;left:565px;top:43px;display:flex;gap:44px;font-size:16px;color:var(--ink)}
.nav .active{color:var(--link)}
.phone-btn{position:absolute;left:907px;top:33px;width:187px;height:40px;border-radius:20px;background:var(--navy);color:#fff;font-size:16px;display:flex;align-items:center;justify-content:center;gap:8px}
.btn{display:inline-flex;align-items:center;gap:10px;background:var(--navy);color:#fff;font-weight:500;font-size:21px;border-radius:32px;padding:0 30px;height:60px}
.hero{left:0;top:104px;width:1200px;height:558px;background:linear-gradient(100deg,#e7eef6 0%,#dfe8f2 40%,#e6c79c 70%,#d9e3ee 100%)}
.hero-title{position:absolute;left:108px;top:162px;color:var(--navy);font-size:44px;font-weight:400;line-height:1}
.hero-title b{display:block;color:var(--blue);font-size:62px;font-weight:700;margin-top:10px}
.hero .btn{position:absolute;left:112px;top:302px}
.section-h{font-size:42px;font-weight:400;letter-spacing:.5px;color:var(--ink)}
.section-h b{font-weight:800}
.rule{width:58px;height:3px;background:var(--blue);margin-top:10px}
.about-photo{left:62px;top:766px;width:502px;height:492px;border-radius:50%;background:var(--navy)}
.about-photo div{position:absolute;left:8px;top:4px;width:494px;height:488px;border-radius:50%;background:linear-gradient(135deg,#6b7f95,#c9a98a 60%,#3c4a5e)}
.about{left:601px;top:770px;width:495px}
.body-text{font-size:16px;line-height:30px;color:var(--text);margin-top:18px}
.about .btn{margin-top:18px}
.companies-h{left:0;top:1372px;width:1200px;text-align:center}
.companies-h .rule{margin:8px auto 0;width:154px}
.logo-box{width:233px;height:91px;border:1.5px solid var(--line);border-radius:10px;display:flex;align-items:center;justify-content:center;font-size:30px;font-weight:700;color:#222;letter-spacing:1px}
.services{left:0;top:1769px;width:1200px;height:888px;background:var(--blue);color:#fff;text-align:center}
.services .section-h{color:#fff;margin-top:76px}
.services .rule{background:#fff;margin:10px auto 0}
.services-sub{font-size:30px;line-height:44px;margin-top:28px}
.services-sub b{font-weight:700}
.card{width:239px;height:210px;border:1.5px solid #7eaee0;border-radius:14px;display:flex;flex-direction:column;align-items:center;justify-content:flex-end;padding-bottom:26px;font-size:22px;color:#fff}
.card svg{width:130px;height:104px;margin-bottom:18px;fill:none;stroke:#fff;stroke-width:3;stroke-linecap:round;stroke-linejoin:round}
.card.active{background:var(--navy);border-color:#fff}
.quote{left:110px;top:2762px;width:475px}
.quote-photo{left:611px;top:2758px;width:492px;height:490px;border-radius:50%;background:linear-gradient(140deg,#c48a3c,#5a4030 45%,#d8c0a0 75%,#8a5a30)}
.contact{left:0;top:3347px;width:1200px;height:666px;background:var(--light)}
.contact-in{position:absolute;left:110px;top:62px;width:900px}
.contact-sub{font-size:30px;line-height:44px;color:#333;margin-top:24px}
.field-label{font-size:16px;font-weight:600;margin-top:26px}
.field{display:flex;height:58px;width:884px;margin-top:10px;background:#fff;border-radius:4px}
.field .ico{width:58px;background:#ddd;display:flex;align-items:center;justify-content:center;border-radius:4px 0 0 4px}
.field span{align-self:center;padding-left:16px;font-size:16px;color:#555}
.contact .btn{margin-top:40px;height:60px}
.footer{left:0;top:4013px;width:1200px;height:519px;background:var(--navy);color:#fff}
.footer .brand{position:absolute;left:370px;top:60px}
.footer .brand-mark{border-color:#fff;width:62px;height:62px}
.footer .brand-name{color:#fff;font-size:34px}
.footer .brand-name b{font-size:40px}
.f-rule{position:absolute;left:95px;width:1010px;height:1.5px;background:#8b98c4}
.f-item{position:absolute;top:216px;display:flex;gap:14px;align-items:flex-start}
.f-ico{width:70px;height:70px;border-radius:50%;background:#fff;border:5px solid var(--blue);display:flex;align-items:center;justify-content:center;flex-shrink:0}
.f-item div p{font-size:13px;line-height:21px}
.f-item div p.t{font-size:16px;font-weight:600;margin-top:4px}
.socials{position:absolute;left:479px;top:350px;display:flex;gap:11px}
.socials i{width:40px;height:40px;border-radius:50%;border:2px solid #fff;display:block}
.copy{position:absolute;left:0;top:437px;width:1200px;text-align:center;font-size:16px}
</style>
</head>
<body>
<div class="abs topbar"></div>

<header class="abs header">
  <div class="brand"><div class="brand-mark"></div><div class="brand-name">BRELLOW COVER<b>INSURANCE LP</b></div></div>
  <nav class="nav"><span class="active">Home</span><span>About</span><span>Our Services</span></nav>
  <div class="phone-btn"><svg width="14" height="14" viewBox="0 0 24 24" fill="#fff"><path d="M6.6 10.8a15 15 0 006.6 6.6l2.2-2.2a1 1 0 011-.25 11.4 11.4 0 003.6.6 1 1 0 011 1V20a1 1 0 01-1 1A17 17 0 013 4a1 1 0 011-1h3.5a1 1 0 011 1c0 1.25.2 2.45.6 3.6a1 1 0 01-.25 1z"/></svg>(555) 318-2740</div>
</header>

<section class="abs hero" role="img" aria-label="Hand stacking wooden blocks into a small house with an insurance block">
  <h1 class="hero-title">BRELLOW COVER<b>INSURANCE LP</b></h1>
  <a class="btn">Get Started <span>&#10230;</span></a>
</section>

<div class="abs about-photo"><div role="img" aria-label="Smiling family of three sitting on the floor making a roof shape with their arms"></div></div>
<section class="abs about">
  <h2 class="section-h">ABOUT</h2>
  <div class="rule"></div>
  <p class="body-text">Brellow Cover Insurance is a full-service, independent insurance agency with over three decades of experience in delivering comprehensive insurance solutions to individuals.</p>
  <p class="body-text" style="margin-top:30px">We proudly offer a diverse portfolio of products from more than 20 of the most reputable and financially secure companies in the industry. Our dedicated team of over 50 skilled professionals is committed to customizing these products and services to meet the unique needs of each client.</p>
  <a class="btn">Read More <span>&#10230;</span></a>
</section>

<div class="abs companies-h"><h2 class="section-h">COMPANIES WE WORK WITH</h2><div class="rule"></div></div>
<div class="abs logo-box" style="left:110px;top:1476px">VARNIX</div>
<div class="abs logo-box" style="left:360px;top:1476px">Ostle</div>
<div class="abs logo-box" style="left:610px;top:1476px;font-size:24px">Meridale Mutual</div>
<div class="abs logo-box" style="left:860px;top:1476px">Quillor</div>
<div class="abs logo-box" style="left:233px;top:1590px">Dunmarrow</div>
<div class="abs logo-box" style="left:483px;top:1590px">KGZ</div>
<div class="abs logo-box" style="left:733px;top:1590px">Pellwick</div>

<section class="abs services">
  <h2 class="section-h">OUR <b>SERVICES</b></h2>
  <div class="rule"></div>
  <p class="services-sub">On <b>Brellow Cover Insurance</b>, LP which sells<br>Homeowners</p>
</section>

<div class="abs card" style="left:108px;top:2068px"><svg viewBox="0 0 130 104"><path d="M10 60l10-26h50l12 26M8 60h80v22H8zM18 82v10M78 82v10"/><circle cx="24" cy="70" r="5"/><circle cx="72" cy="70" r="5"/><path d="M96 30l16 6v18c0 12-8 20-16 24-8-4-16-12-16-24V36z"/><path d="M89 52l6 6 10-12"/></svg>Auto</div>
<div class="abs card active" style="left:358px;top:2068px"><svg viewBox="0 0 130 104"><path d="M30 80c10 0 18-6 26-6h20c4 0 4-6 0-6H62M30 92l10-4 30 2 24-16c4-3 0-8-4-6L74 78"/><path d="M66 20h18v30H66zM72 30h6M72 38h6"/></svg>Renters</div>
<div class="abs card" style="left:609px;top:2068px"><svg viewBox="0 0 130 104"><path d="M22 96V12h40v84M62 96V30h46v66M14 96h102M32 22h6M46 22h6M32 36h6M46 36h6M32 50h6M46 50h6M72 42h6M90 42h6M72 56h6M90 56h6M72 70h6M90 70h6M36 96V80h12v16"/></svg>Condo</div>
<div class="abs card" style="left:860px;top:2068px"><svg viewBox="0 0 130 104"><path d="M36 60l28-26 28 26M44 54v24h40V54M58 78V64h12v14M18 86c8-6 16 6 24 0s16 6 24 0 16 6 24 0 16 6 24 0M30 30a10 10 0 0120-4 8 8 0 0110 12H30a6 6 0 010-8z"/></svg>Flood</div>
<div class="abs card" style="left:108px;top:2310px"><svg viewBox="0 0 130 104"><circle cx="44" cy="70" r="18"/><circle cx="44" cy="70" r="6"/><circle cx="52" cy="22" r="7"/><path d="M52 30v24h20l8 20M88 40h18v56M96 40V20"/></svg>Disability</div>
<div class="abs card" style="left:358px;top:2310px"><svg viewBox="0 0 130 104"><path d="M10 40h110M65 20v60M45 92h40M65 80l-14 12M65 80l14 12M14 40v-16h30v16M24 24v-6h10v6M84 40l16-16 16 16M88 40v-8M104 40v-8"/></svg>Life</div>
<div class="abs card" style="left:609px;top:2310px"><svg viewBox="0 0 130 104"><path d="M25 50a40 40 0 0180 0c-6-6-14-6-20 0-6-6-14-6-20 0-6-6-14-6-20 0-6-6-14-6-20 0zM65 10v40M45 96V68l20-16 20 16v28zM58 96V80h14v16"/></svg>Umbrella</div>
<div class="abs card" style="left:860px;top:2310px"><svg viewBox="0 0 130 104"><circle cx="54" cy="18" r="7"/><path d="M44 32h20v30M46 96V32M62 96V62M70 48l18 6v16c0 10-8 16-18 20"/><path d="M70 66l5 5 9-10"/></svg>Health Insurance</div>

<section class="abs quote">
  <h2 class="section-h">GET A <b>QUOTE</b></h2>
  <div class="rule"></div>
  <p class="body-text">We believe that securing your home is one of the most important decisions you can make. Obtaining a comprehensive insurance quote is essential to understanding your coverage options and ensuring that your property is adequately protected against unforeseen events.</p>
  <p class="body-text" style="margin-top:30px">Our team of experienced professionals is here to guide you through the process, helping you find the right policy that meets your specific needs and budget.</p>
  <a class="btn" style="margin-top:32px">Read More <span>&#10230;</span></a>
</section>
<div class="abs quote-photo" role="img" aria-label="Agent reviewing house plans with a young couple"></div>

<section class="abs contact">
  <div class="contact-in">
    <h2 class="section-h">CONTACT <b>US</b></h2>
    <div class="rule" style="width:80px"></div>
    <p class="contact-sub">Just Some basic information The address of your Personal property will help in finding the right local agent for you</p>
    <p class="field-label">Enter the address of your insurable property</p>
    <div class="field"><div class="ico"><svg width="20" height="20" viewBox="0 0 24 24" fill="none" stroke="#222" stroke-width="3"><circle cx="10" cy="10" r="7"/><path d="M15 15l6 6"/></svg></div><span>Start typing your insurable property</span></div>
    <p class="field-label">Zip code (required)</p>
    <div class="field"><div class="ico"><svg width="16" height="22" viewBox="0 0 16 22"><path d="M8 0a8 8 0 00-8 8c0 6 8 14 8 14s8-8 8-14a8 8 0 00-8-8z" fill="#222"/><circle cx="8" cy="8" r="3" fill="#ddd"/></svg></div><span>Zip code</span></div>
    <a class="btn">Next <span>&#10230;</span></a>
  </div>
</section>

<footer class="abs footer">
  <div class="brand"><div class="brand-mark"></div><div class="brand-name">BRELLOW COVER<b>INSURANCE LP</b></div></div>
  <div class="f-rule" style="top:197px"></div>
  <div class="f-item" style="left:115px"><div class="f-ico"><svg width="22" height="30" viewBox="0 0 16 22"><path d="M8 0a8 8 0 00-8 8c0 6 8 14 8 14s8-8 8-14a8 8 0 00-8-8z" fill="#0e5fa8"/><circle cx="8" cy="8" r="3" fill="#fff"/></svg></div><div><p class="t">Address:</p><p>Sed ut perspiciatis unde omnis iste natus<br>error sit voluptatem accusantium</p></div></div>
  <div class="f-item" style="left:523px"><div class="f-ico"><svg width="28" height="28" viewBox="0 0 24 24" fill="#0e5fa8"><path d="M6.6 10.8a15 15 0 006.6 6.6l2.2-2.2a1 1 0 011-.25 11.4 11.4 0 003.6.6 1 1 0 011 1V20a1 1 0 01-1 1A17 17 0 013 4a1 1 0 011-1h3.5a1 1 0 011 1c0 1.25.2 2.45.6 3.6a1 1 0 01-.25 1z"/></svg></div><div><p class="t">Let's Talk</p><p>Phone : 555-210-4477<br>Fax : 555-210-4478</p></div></div>
  <div class="f-item" style="left:800px"><div class="f-ico"><svg width="30" height="22" viewBox="0 0 30 22"><rect width="30" height="22" rx="3" fill="#0e5fa8"/><path d="M2 3l13 10L28 3" stroke="#fff" stroke-width="2.5" fill="none"/></svg></div><div><p class="t">Email Us</p><p>hello@brellowcover.com</p></div></div>
  <div class="f-rule" style="top:306px"></div>
  <div class="socials" aria-label="Social links"><i></i><i></i><i></i><i></i><i></i></div>
  <p class="copy">Copyright &copy; 2025&nbsp; Brellow Cover Insurance, LP All rights reserved.</p>
</footer>
</body>
</html>
```